Brightmoor - a website to encourage people to spend time in nature

I have a squarespace site with some content on it but the squarespace template doesn't completely suit my needs, I keep fiddling with the template but actually I need some professional help to get it looking the way I want and with the right 'mood'.
The website is for "Brightmoor" - it will be a blog where I write about the importance of nature for good health. I also want to use the website to market services such as outdoor coaching, retreats and walking workshops.
This has been in my head for a LONG time and I currently only use instagram for micro-blogs but it's time for me to get this moving. I've previously engaged other designers on branding for it but they just didn't get it quite the way that I wanted it and I wasn't completely happy with the results. It's been a process for me as to what I want but in the meantime I just didn't come back to the design aspect of it now. I'm looking for a designer who understands the purpose of the website, the ethos and can help me realise this into a design that's clean, clear and simple.

Please note that I have a domain (brightmoor.org) and a lot of content drafted on squarespace already. I have published it with password protection - password is brightmoor2020 - it still has some of the original template on it, but does have some content. Don't take it as anything to follow in particular, i am looking for fresh eyes and fresh ideas.

Target Market(s)

There are three main groups that I want to target - people who are suffering from stress and anxiety, people who treat them and parents who want to get their kids outside (thereby preventing stress and anxiety)

Contact Information for Business Card

Joan Petrie
Brightmoor
Telephone +44 7700 900417
brightmoor@mailvane.com

Logo Text

Brightmoor - if that. I have an idea that the logo should have a leaf on it somewhere, or maybe just be a leaf.

Coding

Coded - Design and coding required

Number of Pages Required

5+ page

Font styles to use
Serif
Sans Serif

Colors
add136
33b8a4
34a6d7
3377b5

Requirements
Must have
• Space for lots of images. The ability for me to edit the pages if I need to. Be user friendly. Look beautiful.
• For an idea of the images I use and the content I'm interested in writing about have a look at @brightmoor on instagram.
• That pop up about cookies so I am complying with data laws.
Should not have
• Must not be too 'busy' I'd like to avoid too much movement.

```html
<!DOCTYPE html>
<html lang="en">
<head>
<meta charset="utf-8">
<title>Brightmoor – Home</title>
<link rel="stylesheet" href="https://fonts.googleapis.com/css2?family=Pinyon+Script&family=Figtree:wght@400;700&display=swap">
<style>
  :root {
    --ink: #000000;
    --panel: #121517;
    --paper: #ffffff;
    --rule: #e2e2e2;
    --text: #1a1a1a;
    --nav-text: #ffffff;
    --forest-light: #b7bab6;
    --forest-mid: #5e7a3e;
    --forest-deep: #2c3a22;
  }
  * { margin: 0; padding: 0; box-sizing: border-box; }
  html, body { width: 1200px; height: 692px; overflow: hidden; background: var(--paper); }
  body { position: relative; font-family: "Figtree", "Helvetica Neue", Arial, sans-serif; color: var(--text); }

  .site-header {
    position: absolute; left: 0; top: 3px; width: 1200px; height: 121px;
    border: 1px solid var(--rule); background: var(--paper);
  }
  .subscribe-button {
    position: absolute; left: 34px; top: 58px; width: 108px; height: 33px;
    background: var(--panel); color: var(--nav-text);
    font-size: 10px; font-weight: 700; letter-spacing: 0.3px; text-transform: uppercase;
    display: flex; align-items: center; justify-content: center;
  }
  .wordmark {
    position: absolute; left: 606px; top: 20px; transform: translateX(-50%);
    font-family: "Pinyon Script", "Times New Roman", serif; font-size: 54px; line-height: 1;
    color: var(--ink); font-weight: 400; white-space: nowrap;
  }

  .hero-photo {
    position: absolute; left: 34px; top: 125px; width: 536px; height: 516px;
    background: linear-gradient(180deg, var(--forest-light) 0%, #8f9f7e 30%, var(--forest-mid) 62%, var(--forest-deep) 100%);
  }
  .hero-bracket { position: absolute; left: 477px; top: 239px; width: 201px; height: 258px; }

  .hero-title {
    position: absolute; left: 597px; top: 313px;
    font-family: "Pinyon Script", "Times New Roman", serif; font-size: 60px; line-height: 1;
    font-weight: 400; color: var(--ink); white-space: nowrap;
  }
  .hero-lede {
    position: absolute; left: 593px; top: 383px;
    font-size: 16px; color: var(--text); white-space: nowrap;
  }

  .nav-panel {
    position: absolute; left: 920px; top: 0; width: 280px; height: 692px;
    background: var(--panel); color: var(--nav-text); z-index: 2;
  }
  .nav-close {
    position: absolute; left: 945px; top: 17px; font-size: 17px; font-weight: 700;
    color: var(--nav-text); z-index: 3;
  }
  .nav-list { list-style: none; }
  .nav-item, .nav-subitem {
    position: absolute; font-size: 17px; line-height: 1; white-space: nowrap;
  }
  .nav-item { left: 49px; }
  .nav-subitem { left: 71px; }
  .nav-toggle {
    position: absolute; left: 63px; top: 8px; width: 15px; height: 3px; background: var(--nav-text);
  }
</style>
</head>
<body>
  <header class="site-header">
    <div class="subscribe-button">Subscribe</div>
    <div class="wordmark">Brightmoor</div>
  </header>

  <div class="hero-photo" role="img" aria-label="Sunlit forest path with tall trees and green grass"></div>

  <svg class="hero-bracket" viewBox="0 0 201 258" aria-hidden="true">
    <path fill="var(--ink)" d="M0 0H201V68H185V16H16V242H185V190H201V258H0Z"/>
  </svg>

  <h1 class="hero-title">Welcome to Brightmoor</h1>
  <p class="hero-lede">The practice of spending time in nature to feel well again</p>

  <span class="nav-close">X</span>
  <nav class="nav-panel">
    <ul class="nav-list">
      <li class="nav-item" style="top:208px">Home</li>
      <li class="nav-item" style="top:261px">About<span class="nav-toggle"></span></li>
      <li class="nav-subitem" style="top:303px">Origin Story</li>
      <li class="nav-subitem" style="top:343px">What We Do</li>
      <li class="nav-subitem" style="top:383px">Partners</li>
      <li class="nav-item" style="top:434px">Blog</li>
      <li class="nav-item" style="top:484px">Contact</li>
    </ul>
  </nav>
</body>
</html>
```